Veltrano.co - Polar Expeditions Specialists

We need a modern, visually striking business card for Veltrano.co, a company specialized in selling expedition cruises to the most remote regions on Earth, with a focus on the Arctic and Antarctica. The design should instantly communicate that the cardholder is an expert in polar travel. Use clean, premium aesthetics with cool tones like icy blue and white, possibly incorporating polar imagery (ice, glaciers, penguins, etc.)

Attached the logo

Contact Information for Business Card

Feels high-end and trustworthy.. Visually memorable — encourages people to keep it

Colors
0054AA
0677BA
7BADD7
CADEEF
E8F1F8

Requirements
Must have
• ice, glaciers, penguins, montains
Nice to have
• modern, transparente,

```html
<!DOCTYPE html>
<html lang="en">
<head>
<meta charset="utf-8">
<title>Veltrano.co – Business Card</title>
<link rel="stylesheet" href="https://fonts.googleapis.com/css2?family=Poppins:wght@400;600;700&family=Arimo:wght@400&display=swap">
<style>
  :root {
    --brand-blue: #2c6db4;
    --brand-deep: #0054aa;
    --ice-light: #e8f1f8;
    --ice-mid: #cadeef;
    --card-white: #f1f1f0;
    --ink: #333333;
    --muted: #666666;
    --rule: #9a9a9a;
    --stage: #3d3d3f;
    --on-blue: #ffffff;
  }
  * { box-sizing: border-box; margin: 0; padding: 0; }
  html, body { width: 1200px; height: 1108px; overflow: hidden; }
  body {
    background: var(--stage);
    position: relative;
    font-family: "Arimo", Arial, sans-serif;
  }
  .card {
    position: absolute;
    left: 290px;
    width: 620px;
    height: 354px;
    border-radius: 2px;
    overflow: hidden;
  }
  .card-front { top: 150px; background: var(--card-white); }
  .card-back  { top: 600px; background: var(--brand-blue); }

  /* front: brand side */
  .brand {
    position: absolute;
    left: 52px;
    top: 136px;
    display: flex;
    align-items: center;
    gap: 14px;
  }
  .brand-dot {
    width: 50px; height: 50px;
    border-radius: 50%;
    background: var(--brand-blue);
    flex: none;
  }
  .brand-name {
    font-family: "Poppins", sans-serif;
    font-weight: 700;
    font-size: 34px;
    line-height: 1;
    color: var(--brand-blue);
  }
  .brand-tagline {
    font-family: "Poppins", sans-serif;
    font-weight: 600;
    font-size: 10.5px;
    color: var(--brand-blue);
    margin-top: 6px;
    letter-spacing: 0.2px;
  }
  .divider {
    position: absolute;
    left: 340px;
    top: 72px;
    width: 1px;
    height: 196px;
    background: var(--rule);
  }

  /* front: contact side */
  .contact {
    position: absolute;
    left: 366px;
    top: 72px;
    color: var(--ink);
  }
  .holder-name {
    font-family: "Poppins", sans-serif;
    font-weight: 700;
    font-size: 25px;
    line-height: 1.05;
    color: var(--brand-blue);
  }
  .holder-role {
    font-size: 12.5px;
    color: var(--muted);
    margin-bottom: 14px;
  }
  .address { font-size: 13.5px; line-height: 1.3; margin-bottom: 12px; }
  .details { list-style: none; font-size: 13.5px; line-height: 1.32; }
  .details li { display: flex; align-items: center; gap: 9px; }
  .details svg { width: 12px; height: 12px; flex: none; fill: var(--brand-blue); }

  /* back */
  .polar-scene {
    position: absolute;
    left: 175px;
    top: 18px;
    width: 270px;
    height: 250px;
    border-radius: 135px 135px 8px 8px;
    background: linear-gradient(180deg, var(--ice-light) 0%, var(--ice-mid) 100%);
  }
  .ice-line {
    position: absolute;
    left: 140px;
    top: 268px;
    width: 340px;
    height: 2px;
    background: var(--ice-light);
    border-radius: 1px;
  }
  .back-url {
    position: absolute;
    left: 0; right: 0;
    top: 292px;
    text-align: center;
    font-size: 14px;
    letter-spacing: 9px;
    color: var(--on-blue);
  }
</style>
</head>
<body>

<section class="card card-front" aria-label="Card front">
  <div class="brand">
    <span class="brand-dot" aria-hidden="true"></span>
    <div>
      <div class="brand-name">Veltrano.co</div>
      <div class="brand-tagline">Polar Expeditions Specialists</div>
    </div>
  </div>

  <div class="divider" aria-hidden="true"></div>

  <div class="contact">
    <div class="holder-name">Mara Ellison</div>
    <div class="holder-role">President</div>
    <p class="address">4216 Glacier Bend Road<br>Whitehorse, Canada 51820</p>
    <ul class="details">
      <li>
        <svg viewBox="0 0 24 24" aria-hidden="true"><path d="M6.6 10.8a15.1 15.1 0 0 0 6.6 6.6l2.2-2.2a1 1 0 0 1 1-.25 11.4 11.4 0 0 0 3.6.57 1 1 0 0 1 1 1V20a1 1 0 0 1-1 1A17 17 0 0 1 3 4a1 1 0 0 1 1-1h3.5a1 1 0 0 1 1 1c0 1.25.2 2.45.57 3.57a1 1 0 0 1-.25 1z"/></svg>
        555-210-4817
      </li>
      <li>
        <svg viewBox="0 0 24 24" aria-hidden="true"><path d="M7 1h10a2 2 0 0 1 2 2v18a2 2 0 0 1-2 2H7a2 2 0 0 1-2-2V3a2 2 0 0 1 2-2zm0 3v14h10V4z"/></svg>
        555-392-6604
      </li>
      <li>
        <svg viewBox="0 0 24 24" aria-hidden="true"><path d="M2 5h20v14H2zm2 2v.4l8 5 8-5V7zm0 2.8V17h16V9.8l-8 5z"/></svg>
        info@veltrano.com
      </li>
      <li>
        <svg viewBox="0 0 24 24" aria-hidden="true"><path d="M12 2a10 10 0 1 0 0 20 10 10 0 0 0 0-20zm0 2a8 8 0 0 1 7.4 5H15V6.5A8 8 0 0 1 12 4zM4.2 13.5 9 18v1.6A8 8 0 0 1 4.2 13.5z"/></svg>
        www.veltrano.com
      </li>
    </ul>
  </div>
</section>

<section class="card card-back" aria-label="Card back">
  <div class="polar-scene" role="img" aria-label="Polar illustration: penguins standing on an ice floe under a starry sky"></div>
  <div class="ice-line" aria-hidden="true"></div>
  <div class="back-url">www.veltrano.com</div>
</section>

</body>
</html>
```